Harlow Vale Boxing Gym's Fennick Trim-Up Contest

Harlow Vale Boxing Gym Presents
“The Fennick Trim-Up Challenge”
Win the fight for fitness and take home awesome prizes.
1st Place Tavlo Mini (16gb) (value $299)
2nd Place One-Month All Access Membership (value $199)
3rd Place Harlow Vale Boxing Gym Training Gloves, T-Shirt and Handwraps (value $79)
(fine print)
* Men’s & Women’s Divisions – two sets of prizes.
* Contestants must register between June 10th and June 15th. Entry fee is $25.
* At registration, contestants will be required to weigh-in in a private setting. For the duration of the competition, actual weight will not be posted; only percent gain or loss.
* Results are based on percentage weight loss as measured on September 19th.
Note: Harlow Vale Boxing Gym reserves the right to cancel the competition in a division if there are fewer than 10 contestants in that division. In that event, a full refund will be issued to participants in that division.

ABOUT US:
HVBG is not a traditional health club with rows of cardio equipment, weight-training machines, or overcrowded step-aerobic classes. Nor are we like old-school boxing or martial arts studios which can oftentimes be scary and uninviting.

Our goal is to strike a balance between instruction, conditioning and fun. We offer over 70 classes per week: mostly boxing, but also muay thai, mixed martial arts ("MMA"), and boot camps. All of our instructors have fought professionally or at the amateur level so they're teaching from experience, not what they learned from an online course.

Target Market(s)

Gym members.

Industry/Entity Type

Fitness

Requirements
Must have
• Our logo (attached) converted to blue.

```html
<!DOCTYPE html>
<html lang="en">
<head>
<meta charset="utf-8">
<title>Harlow Vale Boxing Gym – The Fennick Trim-Up Challenge</title>
<link rel="stylesheet" href="https://fonts.googleapis.com/css2?family=Anton&family=Open+Sans:ital,wght@0,400;0,600;1,400;1,700&family=Raleway:wght@200&display=swap">
<style>
  :root {
    --sky: #8de8fa;
    --red: #f0304a;
    --royal: #2032e8;
    --lime: #e8f83e;
    --sun: #eef53a;
    --ink: #1a1a1a;
    --star: #3fd8f0;
    --white: #ffffff;
  }
  * { margin: 0; padding: 0; box-sizing: border-box; }
  html, body { width: 800px; height: 1200px; overflow: hidden; background: var(--white); }
  .poster { position: relative; width: 800px; height: 1200px; overflow: hidden; background: var(--white); color: var(--ink); font-family: "Open Sans", sans-serif; }

  .presenter { position: absolute; top: 0; left: 0; width: 800px; height: 96px; display: flex; align-items: center; justify-content: center; font-family: "Open Sans", sans-serif; font-weight: 600; font-size: 34px; color: #111; }

  .hero { position: absolute; top: 96px; left: 0; width: 800px; height: 428px; background: var(--sky); }
  .sun-art { position: absolute; left: 30px; top: 18px; width: 316px; height: 316px; border-radius: 50%; background: radial-gradient(circle, var(--sun) 55%, rgba(238,245,58,0.55) 72%, rgba(238,245,58,0) 100%); }

  .title { position: absolute; left: 340px; top: 22px; width: 404px; text-align: center; color: var(--red); font-family: "Anton", sans-serif; line-height: 1; }
  .title .word { display: block; font-size: 84px; letter-spacing: 1px; }
  .title .word.first { font-size: 80px; }
  .title .thin { display: block; font-family: "Raleway", sans-serif; font-weight: 200; font-size: 70px; letter-spacing: -1px; margin: 4px 0 6px; }

  .tagline { position: absolute; left: 0; top: 366px; width: 800px; text-align: center; font-style: italic; font-weight: 700; font-size: 25px; color: #111; }

  .prizes { position: absolute; top: 524px; left: 0; width: 800px; height: 227px; display: flex; font-family: "Anton", sans-serif; text-align: center; line-height: 1.12; }
  .prize { flex: 1; display: flex; flex-direction: column; justify-content: center; align-items: center; padding: 0 10px; }
  .prize.gold { background: var(--royal); color: var(--white); }
  .prize.silver { background: var(--lime); color: var(--royal); }
  .prize.bronze { background: var(--royal); color: var(--white); }
  .gold .rank { font-size: 40px; }
  .gold .item { font-size: 54px; }
  .gold .spec { font-size: 27px; }
  .gold .value { font-size: 38px; }
  .silver .rank, .bronze .rank { font-size: 30px; margin-bottom: 10px; }
  .silver .item { font-size: 25px; }
  .silver .value { font-size: 24px; margin-top: 12px; }
  .bronze .item { font-size: 21px; line-height: 1.35; }
  .bronze .value { font-size: 24px; margin-top: 10px; }

  .rules { position: absolute; left: 112px; top: 782px; width: 620px; list-style: none; font-size: 19px; line-height: 25px; color: #111; }
  .rules li { position: relative; padding-left: 28px; margin-bottom: 15px; }
  .rules li::before { content: "✸"; position: absolute; left: 4px; top: 0; color: var(--star); font-size: 18px; }

  .fine-print { position: absolute; left: 64px; top: 1052px; width: 410px; font-style: italic; font-size: 12px; line-height: 17px; color: #111; }

  .brand { position: absolute; left: 507px; top: 1046px; width: 258px; font-family: "Anton", sans-serif; font-size: 38px; line-height: 1.05; color: var(--royal); text-align: center; }
</style>
</head>
<body>
<main class="poster">
  <header class="presenter">Harlow Vale Boxing Gym Presents</header>

  <section class="hero">
    <div class="sun-art" role="img" aria-label="Illustration of a smiling yellow summer sun with radiating rays"></div>
    <h1 class="title">
      <span class="word first">The</span>
      <span class="word">Fennick</span>
      <span class="thin">TRIM-UP</span>
      <span class="word">Challenge</span>
    </h1>
    <p class="tagline">Win the fight for fitness and take home awesome prizes!</p>
  </section>

  <section class="prizes">
    <div class="prize gold">
      <span class="rank">1st Place</span>
      <span class="item">Tavlo Mini</span>
      <span class="spec">(16gb)</span>
      <span class="value">(value $299)</span>
    </div>
    <div class="prize silver">
      <span class="rank">2nd Place</span>
      <span class="item">One-Month All<br>Access Membership</span>
      <span class="value">(value $199)</span>
    </div>
    <div class="prize bronze">
      <span class="rank">3rd Place</span>
      <span class="item">Harlow Vale Boxing<br>Gym Training Gloves,<br>T-Shirt and Handwraps</span>
      <span class="value">(value $79)</span>
    </div>
  </section>

  <ul class="rules">
    <li>Men’s &amp; Women’s Divisions – two sets of prizes.</li>
    <li>Contestants must register between June 10th and June 15th. Entry fee is $25.</li>
    <li>At registration, contestants will be required to weigh-in in a private setting. For the duration of the competition, actual weight will not be posted; only percent gain or loss.</li>
    <li>Results are based on percentage weight loss as measured on September 19th.</li>
  </ul>

  <p class="fine-print">Note: Harlow Vale Boxing Gym reserves the right to cancel the competition in a division if there are fewer than 10 contestants in that division. In that event, a full refund will be issued to participants in that division.</p>

  <div class="brand">Harlow Vale Boxing</div>
</main>
</body>
</html>
```